Business Card Design Project for a Restaurant/Wine Bar

New, fresh business card design for Brevenna Wine Bar & Restaurant, Bandon, Oregon. We are an established restaurant on the Oregon coast featuring "Italian coastal cuisine."

"Brevenna" means bay leaf in Italian. We aren't sure if we would like our logo on the card or not, but if you have something interesting that uses it, then please do so. The basic information is essential - full restaurant name, address, phone and website (do not use www). The font on our menu and wine list may give you some sort of an idea of our style.

One-sided card needed as we often use the backside to write down various types of info for customers.
Updates

After seeing a few submissions, we would like to see what designers can come up with-using the logo, just the leaf, or none at all. Sky is the limit as long as our full restaurant name, address, phone and website (please leave out www) are there. Please contact us if questions!

I appreciate all of your designs! Our deadline is next week, but I will continue to give feedback on designs as I can. This is our busiest season, so my co-owner/chef/husband, won't have time to look at the designs for awhile. When he does, we can make our decision.

cheers,
Maren

Target Market(s)

Fine dining/wine crowd. Would like something simple and elegant, but not pretentious or stuffy. Brevenna means bay laurel (bay leaf) in Italian (please see our logo).

Industry/Entity Type

Restaurant

Requirements
Must have
• Full Name of Restaurant: Brevenna Wine Bar & Restaurant
Address: 812 4th Ave NW, Harrow Point, Westmere 00417
Phone: 541.555.0172
website: brevennawinebar.example (do not use www)
Should not have
• Loud colors.

```html
<!DOCTYPE html>
<html lang="en">
<head>
<meta charset="utf-8">
<title>Brevenna Wine Bar &amp; Restaurant – Business Card</title>
<link rel="stylesheet" href="https://fonts.googleapis.com/css2?family=Source+Sans+3:wght@400;600;700&display=swap">
<style>
  :root {
    --backdrop: #ece9e2;
    --card: #ffffff;
    --fold-light: #a3a3a3;
    --fold-dark: #3a3a3a;
    --fold-mid: #6b6b6b;
    --ink: #1f1f1f;
    --text: #555555;
    --on-fold: #ffffff;
  }
  html, body {
    margin: 0;
    width: 1200px;
    height: 801px;
    overflow: hidden;
    background: var(--backdrop);
    font-family: "Source Sans 3", sans-serif;
  }
  .card {
    position: absolute;
    left: 100px;
    top: 115px;
    width: 1000px;
    height: 571px;
    background: var(--card);
    box-shadow: 0 6px 24px rgba(0,0,0,0.15);
    overflow: hidden;
  }
  .page-curl {
    position: absolute;
    inset: 0;
  }
  .phone {
    position: absolute;
    top: 42px;
    right: 46px;
    display: flex;
    align-items: center;
    gap: 8px;
    color: var(--on-fold);
    font-size: 32px;
    font-weight: 400;
    letter-spacing: 0.5px;
    line-height: 1;
  }
  .phone svg { width: 26px; height: 26px; }
  .brand-name {
    position: absolute;
    left: 78px;
    top: 210px;
    margin: 0;
    color: var(--ink);
    font-size: 100px;
    font-weight: 700;
    line-height: 1;
    letter-spacing: 1px;
  }
  .website {
    position: absolute;
    right: 50px;
    top: 438px;
    display: flex;
    align-items: center;
    gap: 8px;
    color: var(--text);
    font-size: 24px;
    line-height: 1;
  }
  .website svg { width: 17px; height: 17px; }
  .contact-row {
    position: absolute;
    left: 80px;
    right: 50px;
    top: 488px;
    display: flex;
    justify-content: space-between;
    align-items: baseline;
    line-height: 1;
  }
  .full-name {
    color: var(--text);
    font-size: 26px;
    font-weight: 700;
    transform: translateY(14px);
  }
  .address {
    color: var(--text);
    font-size: 24px;
    font-weight: 400;
  }
</style>
</head>
<body>
  <div class="card">
    <svg class="page-curl" width="1000" height="571" viewBox="0 0 1000 571" aria-hidden="true">
      <defs>
        <linearGradient id="curlShade" x1="0" y1="0" x2="1" y2="1">
          <stop offset="0" stop-color="var(--fold-mid)"/>
          <stop offset="0.55" stop-color="var(--fold-dark)"/>
          <stop offset="1" stop-color="var(--fold-mid)"/>
        </linearGradient>
      </defs>
      <polygon points="390,0 1000,0 1000,235" fill="var(--fold-light)"/>
      <path d="M390,0 L1000,235 C955,240 915,262 900,330 C820,210 620,100 390,0 Z" fill="url(#curlShade)"/>
    </svg>

    <div class="phone">
      <svg viewBox="0 0 24 24" aria-hidden="true">
        <circle cx="12" cy="12" r="10.5" fill="none" stroke="currentColor" stroke-width="1.6"/>
        <path d="M9 6.5c-1 .5-1.8 1.6-1.5 3.2.5 2.8 3 6 5.6 7.3 1.4.7 2.7.3 3.4-.6l-2-2-1.3.8c-1.2-.6-2.6-2.3-3-3.6l1.1-1z" fill="currentColor"/>
      </svg>
      <span>541.555.0172</span>
    </div>

    <h1 class="brand-name">Brevenna</h1>

    <div class="website">
      <svg viewBox="0 0 24 24" aria-hidden="true">
        <circle cx="12" cy="12" r="10" fill="none" stroke="currentColor" stroke-width="2"/>
        <ellipse cx="12" cy="12" rx="4.5" ry="10" fill="none" stroke="currentColor" stroke-width="1.6"/>
        <line x1="2" y1="12" x2="22" y2="12" stroke="currentColor" stroke-width="1.6"/>
      </svg>
      <span>brevennawinebar.example</span>
    </div>

    <div class="contact-row">
      <div class="full-name">Brevenna Wine Bar &amp; Restaurant</div>
      <div class="address">812 4th Ave NW, Harrow Point, Westmere 00417</div>
    </div>
  </div>
</body>
</html>
```